Heron Dusk business card design

I make handmade colourful women's beaded jewellery (necklaces and earnings).
I require a business card to be designed to truly reflect my jewellery, that is, it is different and stands out.
I would like the business card to look creative, arty, gentle and feminine and fit in with the look of my website and logo (already developed).
I would like the business card to have strong use of the water reeds that are flowing in the wind (please see the banner image on my website www.herondusk.net and attached files).

Target Market(s)

Women who are fashion conscious, hip and funky. My audience like things that are a little different and stand out in a crowd.These women are aged in their 20's-40's.

Industry/Entity Type

Jewelry

Contact Information for Business Card

Please include the following items:
1) my logo: Heron Dusk
2) my name, address and phone number: Darla Fontenot, Sydney, Australia, 0498 315 270
3) my web details: www.herondusk.net, info@herondusk.net, www.friendhub.net/herondusk

Font styles to use
Other font styles liked:
• Remachine Script

Requirements
Must have
• My business card must have the following:
• 1) my personal details including all my website contacts (see above).
• 2) Heron Dusk logo
• 3) Reeds flowing in the wind (see my banner image on my website www.herondusk.net or see attached files).
Nice to have
• A sunrise in the background (rising over water)
• I would prefer that the colour scheme to fit with the Heron Dusk logo, that is the colours of an early morning sunrise i.e yellows, oranges. The use of black and white is fine.
Should not have
• I do not like a commercial manufactured look with hard edges. I would like a look that is soft and reflects an artistic, creative and independent business.

```html
<!DOCTYPE html>
<html lang="en">
<head>
<meta charset="utf-8">
<title>Heron Dusk – Business Card</title>
<link rel="stylesheet" href="https://fonts.googleapis.com/css2?family=Open+Sans:wght@400;600&display=swap">
<style>
  :root {
    --page: #e9e6e2;
    --card-dark: #232323;
    --card-light: #ffffff;
    --accent: #f6c400;
    --sun-light: #ffe04a;
    --sun-mid: #f9b90f;
    --sun-deep: #f08a12;
    --ink: #1a1a1a;
    --text-light: #ffffff;
  }
  * { box-sizing: border-box; margin: 0; padding: 0; }
  html, body {
    width: 1189px; height: 1200px; overflow: hidden;
    background: var(--page);
    font-family: "Open Sans", Arial, sans-serif;
  }
  .card {
    position: absolute; left: 140px; width: 916px; height: 522px;
    border-radius: 37px; overflow: hidden;
    box-shadow: 0 6px 14px rgba(0,0,0,.25);
  }
  .card--front { top: 45px; background: var(--card-light); }
  .card--back  { top: 624px; background: var(--card-dark); }
  .card__bg { position: absolute; inset: 0; }
  .brand-mark { position: absolute; }
  .brand-name {
    position: absolute; font-weight: 600; white-space: nowrap;
    transform: translateX(-50%); line-height: 1.2;
  }
  .card--front .brand-name { left: 233px; top: 16px; font-size: 36px; color: var(--ink); }
  .card--back .brand-name { left: 453px; top: 80px; font-size: 46px; color: var(--text-light); }
  .holder {
    position: absolute; right: 51px; top: 244px;
    font-size: 33px; font-weight: 600; color: var(--text-light);
  }
  .contacts {
    position: absolute; right: 51px; top: 305px;
    list-style: none; color: var(--text-light);
  }
  .contacts li {
    display: flex; align-items: center; justify-content: flex-end;
    height: 36.5px; font-size: 24px; font-weight: 400; white-space: nowrap;
  }
  .contacts .icon {
    width: 21px; height: 21px; margin-left: 20px;
    background: var(--text-light); border-radius: 2px;
    display: flex; align-items: center; justify-content: center;
    flex: none;
  }
</style>
</head>
<body>

<section class="card card--front">
  <svg class="card__bg" width="916" height="522" viewBox="0 0 916 522">
    <path d="M0 222 C 220 230, 300 250, 420 222 C 600 180, 760 176, 916 172 L916 522 L0 522 Z" fill="var(--accent)"/>
    <path d="M0 250 C 220 250, 300 262, 420 234 C 600 190, 760 182, 916 178 L916 522 L0 522 Z" fill="var(--card-dark)"/>
  </svg>
  <svg class="brand-mark" style="left:77px;top:76px" width="312" height="312" viewBox="0 0 312 312">
    <defs>
      <linearGradient id="sunFront" x1="0" y1="0" x2="0" y2="1">
        <stop offset="0" stop-color="var(--sun-light)"/>
        <stop offset=".6" stop-color="var(--sun-mid)"/>
        <stop offset="1" stop-color="var(--sun-deep)"/>
      </linearGradient>
    </defs>
    <circle cx="156" cy="156" r="156" fill="var(--card-light)"/>
    <circle cx="156" cy="156" r="148" fill="var(--ink)"/>
    <circle cx="156" cy="156" r="142" fill="url(#sunFront)" role="img" aria-label="Round brand emblem in warm yellow and orange tones"/>
  </svg>
  <div class="brand-name">Heron Dusk</div>

  <div class="holder">Darla Fontenot</div>
  <ul class="contacts">
    <li>0498 315 270
      <span class="icon"><svg width="13" height="13" viewBox="0 0 24 24"><path d="M6.6 10.8a15 15 0 0 0 6.6 6.6l2.2-2.2c.3-.3.7-.4 1-.2 1.1.4 2.3.6 3.6.6.6 0 1 .4 1 1V20c0 .6-.4 1-1 1A17 17 0 0 1 3 4c0-.6.4-1 1-1h3.5c.6 0 1 .4 1 1 0 1.3.2 2.5.6 3.6.1.3 0 .7-.2 1z" fill="var(--card-dark)"/></svg></span></li>
    <li>info@herondusk.net
      <span class="icon"><svg width="14" height="11" viewBox="0 0 14 11"><rect x="0.5" y="0.5" width="13" height="10" fill="var(--card-dark)"/><path d="M1 1l6 5 6-5" stroke="var(--text-light)" fill="none"/></svg></span></li>
    <li>www.herondusk.net
      <span class="icon"><svg width="15" height="15" viewBox="0 0 16 16"><circle cx="8" cy="8" r="7" fill="none" stroke="var(--card-dark)" stroke-width="1.6"/><path d="M1 8h14M8 1c-3 3.5-3 10.5 0 14M8 1c3 3.5 3 10.5 0 14" stroke="var(--card-dark)" stroke-width="1.2" fill="none"/></svg></span></li>
    <li>www.friendhub.net/herondusk
      <span class="icon"><svg width="11" height="11" viewBox="0 0 12 12"><rect x="1" y="1" width="10" height="10" fill="var(--card-dark)"/></svg></span></li>
    <li>Wattle Cove, Australia
      <span class="icon"><svg width="12" height="15" viewBox="0 0 12 16"><path d="M6 0a6 6 0 0 0-6 6c0 4.5 6 10 6 10s6-5.5 6-10a6 6 0 0 0-6-6z" fill="var(--card-dark)"/><circle cx="6" cy="6" r="2.2" fill="var(--text-light)"/></svg></span></li>
  </ul>
</section>

<section class="card card--back">
  <svg class="brand-mark" style="left:290px;top:147px" width="326" height="326" viewBox="0 0 326 326">
    <defs>
      <linearGradient id="sunBack" x1="0" y1="0" x2="0" y2="1">
        <stop offset="0" stop-color="var(--sun-light)"/>
        <stop offset=".6" stop-color="var(--sun-mid)"/>
        <stop offset="1" stop-color="var(--sun-deep)"/>
      </linearGradient>
    </defs>
    <circle cx="163" cy="163" r="163" fill="#111111"/>
    <circle cx="163" cy="163" r="155" fill="url(#sunBack)" role="img" aria-label="Round brand emblem in warm yellow and orange tones"/>
  </svg>
  <div class="brand-name">Heron Dusk</div>
</section>

</body>
</html>
```